Etiketten-Design für einen importierten Honig
Zielgruppe
Wir importieren originalen Manuka Honig aus Neuseeland. Der Manuka Honig ist bekannt für seine besonderen Eigenschaften (antibakteriell, etc.). Ein Glas unseres Honigs (500g) kostet zwischen 30 und 150 EUR.
Unsere Zielgruppe sind gesundheitsbewusste Kunden, die wenig preissensibel sind. Überwiegend wird der Manuka Honig im Fachhandel (z.B. Reformhaus, Drogerie, Biomarkt, etc.) verkauft. Der Großteil unserer Kunden ist 30+ Jahre.
Aufgabenstellung
Bei dem Etikett handelt es sich um das erste Produktetikett. Damit ist in der Farbgestaltung noch alles offen. Das Logo und der Name ist jedoch fix.
Das Etikett ist wird auf einem bpa-freien schwarzen Plastikbehälter angebracht. Dieser ist bei Manuka Honigen Standard aufgrund des langen Transports von Neuseeland nach Deutschland (gerne googeln). Der Deckel dieses Behälters ist schwarz.
Nachdem es sich um ein hochpreisiges Produkt handelt, soll das Etikett diese hohe Wertigkeit widerspiegeln. Damit ist eine Veredelung des Etiketts notwendig. Viele Konkurrenten arbeiten mit Gold, alternative Farben sind jedoch auch möglich.
Das Etikett überdeckt drei der vier Seiten des Plastikbehälters (vorne + links + rechts). Die Maße sind 160 mm x 60 mm. Zusätzlich zu den Etikettenmaßen bitte 2 mm Beschnittzugabe je Seite hinzufügen.
Hintergrundinformationen zu unserer Marke:
- Der Markenname lautet Kalvio. Der Markenname leitet sich von der ersten Imkerin Neuseelands ab - Edith Carrow. Sie hatte im Jahr 1839 die ersten Bienenstöcke nach Neuseeland gebracht und den ersten Manuka Honig geerntet.
- Unser Logo ist eine Verbindung einer Frau und den neuseeländischen Farn. Dieses Logo stellt also direkt eine Verbindung zu Neuseeland dar.
- Unsere Marke Kalvio ist eine qualitativ hochwertige, luxuriöse und hochpreisige Marke. Genau wie in dem Logo selbst, sollen diese Verbindungen zu Neuseeland, der Natur (Honig ist ein Naturprodukt) und Edith Carrow auch auf dem Etikett zu finden sein.
Wonach suchen wir:
- Wir sind auf der Suche nach einem einzigartigen Design, der unseren Honig besonders hervorhebt. Das Etikett soll auffällig sein und uns von anderen unterscheiden. (Eye-catching)
- Eine Veredelung des Etiketts ist Pflicht, da dies für uns die Wertigkeit des Etiketts und des Produktes stark erhöht. In welcher Art die Veredelung durchgeführt wird, ist Ihnen überlassen.
Das dürfen Sie frei wählen:
- Bisher haben..

```html
<!DOCTYPE html>
<html lang="de">
<head>
<meta charset="utf-8">
<title>Kalvio Manuka Honig – Etikett</title>
<link rel="stylesheet" href="https://fonts.googleapis.com/css2?family=Cormorant+Garamond:wght@500&family=Montserrat:wght@500;600&family=Great+Vibes&display=swap">
<style>
  :root {
    --stage: #d9d9d9;
    --label-black: #0c0c0c;
    --blob-grey: #3a3a3c;
    --blob-grey-soft: #2a2a2c;
    --gold: #d6b06a;
    --gold-deep: #b8893c;
    --badge-amber: #f5b21a;
    --badge-yellow: #ffd84a;
    --white: #ffffff;
    --art-tint: rgba(214, 176, 106, 0.18);
  }
  * { margin: 0; padding: 0; box-sizing: border-box; }
  html, body { width: 1200px; height: 1200px; overflow: hidden; }
  body { background: var(--stage); position: relative; }

  .label {
    position: absolute; left: 72px; top: 105px;
    width: 1057px; height: 990px;
    background: var(--label-black);
    overflow: hidden;
  }
  .label-blobs { position: absolute; inset: 0; }

  .art { position: absolute; background: var(--art-tint); border-radius: 46%; }
  .art-flower-left { left: 4px; top: 36px; width: 297px; height: 477px; border-radius: 48% 52% 40% 60%; }
  .art-flower-right { left: 706px; top: 10px; width: 288px; height: 240px; }
  .art-bee { left: 832px; top: 306px; width: 135px; height: 117px; }
  .art-flower-bottom { left: 49px; top: 783px; width: 153px; height: 162px; }

  .brand-mark {
    position: absolute; left: 468px; top: 85px;
    width: 120px; height: 120px; border-radius: 50%;
    border: 3px solid var(--gold);
  }
  .brand-name {
    position: absolute; left: 0; width: 1016px; top: 280px;
    text-align: center;
    font-family: "Cormorant Garamond", serif; font-weight: 500;
    font-size: 46px; letter-spacing: 0.22em; color: var(--gold);
  }
  .product-name {
    position: absolute; left: 0; width: 1016px; top: 405px;
    text-align: center;
    font-family: "Montserrat", sans-serif; font-weight: 600;
    font-size: 124px; letter-spacing: 0.02em; color: var(--white);
    line-height: 1;
  }
  .product-type {
    position: absolute; left: 211px; width: 445px; top: 520px;
    text-align: center;
    font-family: "Great Vibes", cursive;
    font-size: 120px; color: var(--gold); line-height: 1;
  }
  .rule { position: absolute; left: 211px; width: 445px; height: 3px; background: var(--gold); }
  .rule-top { top: 616px; }
  .rule-bottom { top: 752px; }
  .origin {
    position: absolute; left: 211px; width: 445px; top: 684px;
    text-align: center;
    font-family: "Montserrat", sans-serif; font-weight: 500;
    font-size: 40px; letter-spacing: 0.03em; color: var(--white);
    line-height: 1.3;
  }
  .grade-badge { position: absolute; left: 670px; top: 585px; width: 230px; height: 290px; }
  .grade-text {
    position: absolute; left: 670px; top: 638px; width: 226px;
    text-align: center;
    font-family: "Montserrat", sans-serif; font-weight: 500;
    font-size: 50px; line-height: 1.05; color: #1a1206;
  }
  .net-weight {
    position: absolute; left: 714px; top: 880px;
    font-family: "Montserrat", sans-serif; font-weight: 500;
    font-size: 40px; color: var(--gold);
  }
</style>
</head>
<body>
  <section class="label">
    <svg class="label-blobs" viewBox="0 0 1057 990" width="1057" height="990" aria-hidden="true">
      <path d="M10 60 C120 0 260 40 300 160 C330 260 250 340 230 430 C210 560 320 650 520 680 L520 990 L0 990 L0 80 Z" fill="var(--blob-grey-soft)"/>
      <path d="M20 90 C110 40 230 70 270 170 C300 250 210 330 190 420 C170 520 120 560 20 560 Z" fill="var(--blob-grey)"/>
      <path d="M690 120 C720 40 800 20 880 50 C940 80 1000 40 1057 60 L1057 300 C980 300 930 260 880 250 C800 240 680 220 690 120 Z" fill="var(--blob-grey)"/>
      <path d="M100 990 C110 900 200 850 300 860 C380 870 420 930 480 990 Z" fill="var(--blob-grey)"/>
    </svg>

    <div class="art art-flower-left" role="img" aria-label="Goldene Linienzeichnung einer Manukablüte"></div>
    <div class="art art-flower-right" role="img" aria-label="Goldene Linienzeichnung einer Manukablüte"></div>
    <div class="art art-bee" role="img" aria-label="Goldene Linienzeichnung einer Biene"></div>
    <div class="art art-flower-bottom" role="img" aria-label="Kleine goldene Manukablüte"></div>

    <div class="brand-mark" aria-hidden="true"></div>
    <div class="brand-name">KALVIO</div>

    <h1 class="product-name">MANUKA</h1>
    <div class="product-type">Honig</div>

    <div class="rule rule-top"></div>
    <div class="origin">AUS NEUSEELAND</div>
    <div class="rule rule-bottom"></div>

    <svg class="grade-badge" viewBox="0 0 230 290" aria-hidden="true">
      <defs>
        <radialGradient id="badgeFill" cx="50%" cy="50%" r="60%">
          <stop offset="0%" stop-color="var(--badge-yellow)"/>
          <stop offset="100%" stop-color="var(--badge-amber)"/>
        </radialGradient>
      </defs>
      <polygon points="115,5 220,63 220,177 115,235 10,177 10,63" fill="none" stroke="var(--gold)" stroke-width="4"/>
      <polygon points="115,22 205,72 205,168 115,218 25,168 25,72" fill="url(#badgeFill)"/>
      <path d="M115 242 C104 258 100 266 100 272 A15 15 0 0 0 130 272 C130 266 126 258 115 242 Z" fill="var(--gold-deep)"/>
    </svg>
    <div class="grade-text">MGO<br>450+</div>

    <div class="net-weight">℮500 g</div>
  </section>
</body>
</html>
```